Veltrane Group Business Card Design

The CEO is looking for a new trendy look for his business card.
You can stay with current branding or come up with something new/creative. It can be 3D, including Medical Office buildings. You can use our logo in a variety of colors. Please include name, title, company name, company website, email address, cell number

Target Market(s)

Real Estate Development and Construction

Industry/Entity Type

Health care real estate

Contact Information for Business Card

Rohesh Kamdar, CEO M-604.781.2249 E-roheshkamdar@veltrane.com Address:4180 Lindqvist Ave, Tampa, FL 33482 www.veltrane.com

Font styles to use
Other font styles liked:
• Be creative

Requirements
Must have
• Creative, trendy look
Nice to have
• Please go to our website to get a feel- www. veltrane.com
Should not have
• small fonts

```html
<!DOCTYPE html>
<html lang="en">
<head>
<meta charset="utf-8">
<title>Veltrane Group Business Card</title>
<link rel="stylesheet" href="https://fonts.googleapis.com/css2?family=Montserrat:wght@400;500;700;800&display=swap">
<style>
  :root {
    --backdrop: #8a7152;
    --card-light: #ffffff;
    --card-dark: #141414;
    --ink: #111111;
    --ink-soft: #1a1a1a;
    --band: #151515;
    --emboss: #1f1f1f;
  }
  * { margin: 0; padding: 0; box-sizing: border-box; }
  html, body { width: 900px; height: 1200px; overflow: hidden; }
  body {
    background: var(--backdrop);
    font-family: "Montserrat", Arial, sans-serif;
    position: relative;
  }
  .card {
    position: absolute;
    width: 743px;
    height: 440px;
    overflow: hidden;
    box-shadow: 0 10px 24px rgba(0,0,0,0.45);
  }
  .card--front { left: 80px; top: 131px; background: var(--card-light); color: var(--ink); }
  .card--back { left: 78px; top: 638px; background: var(--card-dark); }

  .bands { position: absolute; inset: 0; }

  .holder { position: absolute; left: 35px; top: 57px; }
  .holder__name { font-weight: 700; font-size: 26px; line-height: 1.1; letter-spacing: 0.2px; }
  .holder__title { font-weight: 400; font-size: 16px; margin-top: 3px; }

  .address { position: absolute; left: 35px; top: 266px; font-size: 16px; line-height: 20px; color: var(--ink-soft); }

  .contacts { position: absolute; left: 35px; top: 325px; list-style: none; }
  .contacts li { display: flex; align-items: center; height: 28px; font-size: 16px; color: var(--ink-soft); }
  .contacts svg { width: 16px; height: 16px; margin-right: 12px; fill: var(--ink); }

  .wordmark {
    position: absolute;
    right: 44px;
    top: 166px;
    text-align: right;
    font-weight: 800;
    color: var(--ink);
    line-height: 1;
  }
  .wordmark__main { display: block; font-size: 66px; letter-spacing: -1px; }
  .wordmark__sub { display: block; font-size: 38px; margin-top: 4px; }

  .wordmark--emboss {
    left: 0; right: 0; top: 150px;
    text-align: center;
    color: var(--emboss);
  }
  .wordmark--emboss .wordmark__main { font-size: 96px; letter-spacing: -2px; }
  .wordmark--emboss .wordmark__sub { font-size: 50px; margin-top: 6px; padding-left: 220px; }
</style>
</head>
<body>
  <section class="card card--front">
    <svg class="bands" viewBox="0 0 743 440" aria-hidden="true">
      <polygon points="527,0 713,0 653,160 468,160" fill="var(--band)"/>
      <polygon points="407,318 585,318 538,440 357,440" fill="var(--band)"/>
    </svg>

    <div class="holder">
      <h1 class="holder__name">Rohesh Kamdar</h1>
      <p class="holder__title">CEO</p>
    </div>

    <p class="address">4180 Lindqvist Ave,<br>Tampa, FL 33482</p>

    <ul class="contacts">
      <li>
        <svg viewBox="0 0 24 24" aria-hidden="true"><path d="M6.6 10.8a15.1 15.1 0 0 0 6.6 6.6l2.2-2.2a1 1 0 0 1 1-.25 11.4 11.4 0 0 0 3.6.57 1 1 0 0 1 1 1V20a1 1 0 0 1-1 1A17 17 0 0 1 3 4a1 1 0 0 1 1-1h3.5a1 1 0 0 1 1 1c0 1.25.2 2.45.57 3.6a1 1 0 0 1-.25 1z"/></svg>
        604.781.2249
      </li>
      <li>
        <svg viewBox="0 0 24 24" aria-hidden="true"><path d="M3 5h18v2l-9 6-9-6zM3 9l9 6 9-6v10H3z"/></svg>
        roheshkamdar@veltrane.com
      </li>
      <li>
        <svg viewBox="0 0 24 24" aria-hidden="true"><path d="M12 2a10 10 0 1 0 0 20 10 10 0 0 0 0-20zm-1 17.9A8 8 0 0 1 4.1 11H8c.1 3.2 1.2 6.3 3 8.9zM8 9H4.1A8 8 0 0 1 11 4.1 16 16 0 0 0 8 9zm2 0a14 14 0 0 1 2-5 14 14 0 0 1 2 5zm0 2h4a14 14 0 0 1-2 7 14 14 0 0 1-2-7zm6 0h3.9a8 8 0 0 1-6.9 6.9A16 16 0 0 0 16 11zm0-2a16 16 0 0 0-3-4.9A8 8 0 0 1 19.9 9z"/></svg>
        www.veltrane.com
      </li>
    </ul>

    <div class="wordmark">
      <span class="wordmark__main">Veltrane</span>
      <span class="wordmark__sub">Group</span>
    </div>
  </section>

  <section class="card card--back">
    <div class="wordmark wordmark--emboss">
      <span class="wordmark__main">Veltrane</span>
      <span class="wordmark__sub">Group</span>
    </div>
  </section>
</body>
</html>
```